Financial Services Consultant needs a business card

We need a business card for a new consulting company based in Melbourne called
"Quelbrook Insights". Tagline is Measure, Monitor, Save
We would like to see business card designs that are in line with the minimal style of the website www.quelbrook-insights.example
The font I have used on the website is Proxima Nova and would like the same or similar font used on the business card with a minimal design in line with the website Two sided with "QUELBROOK INSIGHTS" MEASURE, MONITOR, SAVE on one side and name, title and contact details on the otther
Updates

Hi All, thanks for your submissions, much appreciated.

I have recently added some colour to my webiste, it is hex #3a7b74 for those that wish to use it
Thanks

Hi all

thanks very much for your design submissions I am very impressed and they are much appreciated.

Interms of general feedback please find below;

Colour: I am trying to stick to a minimal design and colour scheme for my website which is still under construction, up to 3 colours( www.quelbrook-insights.example) it is currently black and white with a small amount of blue/green but I am open to suggestion/interpretations for a consulting company.

Card: I dont mind if it has rounded edges or straight, I was thinking about using a letterpress card if possible

Detail: the detail on the card will include; Name, Title, Mobile, Personal Email, Business Email,Web,Business Address

Once again thanks for submissions

Industry/Entity Type

Business

```html
<!DOCTYPE html>
<html lang="en">
<head>
<meta charset="utf-8">
<title>Quelbrook Insights — Business Card</title>
<link href="https://fonts.googleapis.com/css2?family=Open+Sans:wght@400;600;700&display=swap" rel="stylesheet">
<style>
  :root {
    --backdrop: #e8e8ee;
    --paper: #ffffff;
    --ink: #111111;
    --text-grey: #3c3c3c;
    --teal: #3a7b74;
    --band-black: #1a1a1a;
  }
  * { margin: 0; padding: 0; box-sizing: border-box; }
  html, body {
    width: 1200px; height: 987px; overflow: hidden;
    background: var(--backdrop);
    font-family: "Open Sans", Arial, sans-serif;
  }
  .stage { position: relative; width: 1200px; height: 987px; }

  .card {
    position: absolute;
    width: 600px; height: 343px;
    background: var(--paper);
    border-radius: 30px;
    overflow: hidden;
    box-shadow: 0 6px 18px rgba(0,0,0,0.12);
  }

  /* Brand side */
  .card--brand { left: 550px; top: 70px; }
  .card--brand .wordmark {
    position: absolute; left: 0; right: 0; top: 110px;
    text-align: center;
    font-weight: 700; font-size: 36px; letter-spacing: 5px;
    color: var(--ink);
  }
  .card--brand .tagline {
    position: absolute; left: 0; right: 0; top: 196px;
    text-align: center;
    font-size: 17px; color: var(--text-grey);
  }
  .card--brand .web {
    position: absolute; left: 0; right: 0; top: 226px;
    text-align: center;
    font-size: 15px; letter-spacing: 3px; color: var(--text-grey);
  }
  .card--brand .web strong { font-weight: 700; }

  /* Contact side */
  .card--contact { left: 50px; top: 560px; }
  .contact__tab {
    position: absolute; left: 0; top: 22px;
    width: 22px; height: 46px; background: var(--teal);
  }
  .contact__name {
    position: absolute; left: 52px; top: 26px;
    font-weight: 700; font-size: 20px; color: var(--text-grey);
  }
  .contact__title {
    position: absolute; left: 52px; top: 54px;
    font-size: 14px; color: var(--teal);
  }
  .contact__address {
    position: absolute; left: 52px; top: 104px;
    font-size: 15px; line-height: 21px; color: var(--text-grey);
  }
  .contact__phone {
    position: absolute; left: 52px; top: 170px;
    font-size: 15px; color: var(--text-grey);
    display: flex; align-items: center; gap: 7px;
  }
  .contact__wordmark {
    position: absolute; right: 30px; top: 136px;
    font-weight: 700; font-size: 27px; letter-spacing: 3px;
    color: var(--ink);
  }
  .contact__bands { position: absolute; left: 0; bottom: 0; }
  .contact__web {
    position: absolute; left: 30px; top: 262px;
    font-size: 14px; color: var(--paper);
  }
</style>
</head>
<body>
<main class="stage">

  <section class="card card--brand" aria-label="Business card, brand side">
    <div class="wordmark">QUELBROOK INSIGHTS</div>
    <div class="tagline">Measure, Monitor, Save</div>
    <div class="web">www.<strong>quelbrook-insights</strong>.example</div>
  </section>

  <section class="card card--contact" aria-label="Business card, contact side">
    <div class="contact__tab"></div>
    <div class="contact__name">Your Name</div>
    <div class="contact__title">Title</div>
    <div class="contact__address">Street Name, City Name<br>State Zip Code</div>
    <div class="contact__phone">
      <svg width="14" height="14" viewBox="0 0 24 24" aria-hidden="true">
        <path fill="#3c3c3c" d="M6.6 10.8a15.1 15.1 0 0 0 6.6 6.6l2.2-2.2a1 1 0 0 1 1-.25 11.4 11.4 0 0 0 3.6.57 1 1 0 0 1 1 1V20a1 1 0 0 1-1 1A17 17 0 0 1 3 4a1 1 0 0 1 1-1h3.5a1 1 0 0 1 1 1c0 1.25.2 2.46.57 3.6a1 1 0 0 1-.25 1z"/>
      </svg>
      123-456-0789
    </div>
    <div class="contact__wordmark">QUELBROOK INSIGHTS</div>

    <svg class="contact__bands" width="600" height="343" viewBox="0 0 600 343" aria-hidden="true">
      <path fill="var(--band-black)" d="M0 268 L300 268 C345 268 350 292 400 292 L600 292 L600 343 L0 343 Z"/>
      <path fill="var(--teal)" d="M0 248 L300 248 C340 248 345 268 380 268 L0 268 Z"/>
      <rect x="0" y="248" width="300" height="20" fill="var(--teal)"/>
    </svg>
    <div class="contact__web" style="top:249px">www.quelbrook-insights.example</div>
  </section>

</main>
</body>
</html>
```